Brookvane Consulting Business Card Design

Business Card Design for Brookvane Consulting. Brookvane Consulting is a boutique consultancy based in Atlanta, GA., that specializes in marketing strategy, organization planning, and leadership development. We provide solutions for small businesses and startups as well as Vantage 300 companies.

http://brookvaneconsulting.com/

Target Market(s)

We provide solutions for small businesses and startups as well as Vantage 300 companies.

Industry/Entity Type

Consulting

Contact Information for Business Card

Two sided business card with priority on contact information, logo, tag line (Inspiration to Dream More, Do More, Become More)

Colors

Designer to choose colors to be used in the design.

Requirements
Must have
• contact information, logo, tag line (Inspiration to Dream More, Do More, Become More)
• Simple no over communication.
Nice to have
• I would like to see different placements of logo and creative use of both sides of the card
Should not have
• Do not put too much information on the card.

```html
<!DOCTYPE html>
<html lang="en">
<head>
<meta charset="utf-8">
<title>Brookvane Consulting – Business Card</title>
<link href="https://fonts.googleapis.com/css2?family=Lato:wght@300;400;700&display=swap" rel="stylesheet">
<style>
  :root {
    --backdrop: #3a3a3a;
    --card-white: #ffffff;
    --card-mist: #e6e6e6;
    --card-dark: #262626;
    --card-dark-edge: #1c1c1c;
    --ink: #1e1e1e;
    --ink-soft: #444444;
    --rule: #555555;
    --silver: #cfcfcf;
    --silver-dim: #9a9a9a;
  }
  * { margin: 0; padding: 0; box-sizing: border-box; }
  html, body { width: 1200px; height: 900px; overflow: hidden; }
  body {
    background: var(--backdrop);
    font-family: "Lato", sans-serif;
    display: flex;
    flex-direction: column;
    align-items: center;
    justify-content: center;
    gap: 28px;
  }
  .card {
    position: relative;
    width: 700px;
    height: 400px;
    border-radius: 22px;
    overflow: hidden;
    box-shadow: 0 12px 30px rgba(0,0,0,0.35);
  }
  /* Front */
  .card-front {
    background: radial-gradient(ellipse at 60% 35%, var(--card-white) 40%, var(--card-mist) 100%);
    color: var(--ink);
  }
  .front-brand {
    position: absolute;
    left: 44px;
    top: 54px;
    display: flex;
    align-items: center;
    gap: 14px;
  }
  .brand-square {
    width: 30px;
    height: 30px;
    background: var(--ink);
  }
  .brand-name {
    font-weight: 400;
    font-size: 40px;
    letter-spacing: 1px;
    color: var(--ink);
  }
  .front-rule {
    position: absolute;
    left: 44px;
    right: 44px;
    top: 198px;
    height: 2px;
    background: var(--rule);
  }
  .person {
    position: absolute;
    right: 44px;
    top: 138px;
    text-align: right;
  }
  .person-name {
    font-weight: 700;
    font-size: 24px;
    letter-spacing: 1px;
    text-transform: uppercase;
  }
  .person-role {
    font-size: 14px;
    color: var(--ink-soft);
    margin-top: 2px;
  }
  .address {
    position: absolute;
    right: 44px;
    top: 214px;
    text-align: right;
    font-size: 17px;
    line-height: 1.5;
    color: var(--ink-soft);
  }
  .contacts {
    position: absolute;
    left: 44px;
    top: 214px;
    list-style: none;
    font-size: 16px;
    line-height: 1.55;
    color: var(--ink-soft);
  }
  .contacts li { display: flex; align-items: center; gap: 10px; }
  .contacts svg { width: 13px; height: 13px; fill: var(--ink-soft); flex: none; }
  .front-swoosh {
    position: absolute;
    left: 0;
    bottom: 0;
    width: 700px;
    height: 400px;
    pointer-events: none;
  }
  /* Back */
  .card-back {
    background: linear-gradient(160deg, var(--card-dark) 0%, var(--card-dark-edge) 100%);
    display: flex;
    flex-direction: column;
    align-items: center;
    justify-content: center;
    gap: 22px;
  }
  .back-brand {
    display: flex;
    align-items: center;
    gap: 18px;
  }
  .back-brand .brand-square { width: 38px; height: 38px; background: var(--silver); }
  .back-brand .brand-name { color: var(--silver); font-size: 52px; }
  .tagline {
    font-weight: 300;
    font-size: 18px;
    letter-spacing: 2px;
    color: var(--silver-dim);
  }
</style>
</head>
<body>

  <section class="card card-front" aria-label="Card front">
    <svg class="front-swoosh" viewBox="0 0 700 400" aria-hidden="true">
      <path d="M0 318 C 150 330, 300 300, 400 400 L 0 400 Z" fill="#8f8f8f"/>
      <path d="M0 326 C 160 338, 290 318, 380 400 L 0 400 Z" fill="#262626"/>
    </svg>

    <div class="front-brand">
      <span class="brand-square"></span>
      <span class="brand-name">Brookvane Consulting</span>
    </div>

    <div class="person">
      <p class="person-name">Daniel Reyes</p>
      <p class="person-role">Director</p>
    </div>

    <div class="front-rule"></div>

    <ul class="contacts">
      <li><svg viewBox="0 0 16 16"><path d="M3 1h3l1.5 4-2 1.3a9 9 0 0 0 4.2 4.2L11 8.5l4 1.5v3a2 2 0 0 1-2 2A13 13 0 0 1 1 3a2 2 0 0 1 2-2z"/></svg>+1 404 555-0182</li>
      <li><svg viewBox="0 0 16 16"><path d="M4 0h8a1 1 0 0 1 1 1v14a1 1 0 0 1-1 1H4a1 1 0 0 1-1-1V1a1 1 0 0 1 1-1zm0 2v10h8V2zm4 11a1 1 0 1 0 0 2 1 1 0 0 0 0-2z"/></svg>+1 404 555-0247</li>
      <li><svg viewBox="0 0 16 16"><path d="M0 3h16v10H0zm1.5 1.2V12h13V4.2L8 9z M2.2 4 8 8l5.8-4z"/></svg>BrookvaneConsulting.com</li>
      <li><svg viewBox="0 0 16 16"><path d="M8 0a8 8 0 1 0 0 16A8 8 0 0 0 8 0zm0 1.5c.9 0 2 1.8 2.3 5H5.7C6 3.3 7.1 1.5 8 1.5zM5.7 8h4.6c-.3 3.2-1.4 5-2.3 5s-2-1.8-2.3-5zM1.6 8h2.6c.1 2 .5 3.6 1.1 4.7A6.5 6.5 0 0 1 1.6 8zm10.2 0h2.6a6.5 6.5 0 0 1-3.7 4.7c.6-1.1 1-2.7 1.1-4.7zM5.3 3.3c-.6 1-1 2.4-1.1 3.2H1.6a6.5 6.5 0 0 1 3.7-3.2zm5.4 0a6.5 6.5 0 0 1 3.7 3.2h-2.6c-.1-.8-.5-2.2-1.1-3.2z"/></svg>www.BrookvaneConsulting.com</li>
    </ul>

    <div class="address">
      <p>1420 Marlow Street NE,</p>
      <p>Atlanta, GA 30309</p>
    </div>
  </section>

  <section class="card card-back" aria-label="Card back">
    <div class="back-brand">
      <span class="brand-square"></span>
      <span class="brand-name">Brookvane Consulting</span>
    </div>
    <p class="tagline">Inspiration to Dream More, Do More, Become More</p>
  </section>

</body>
</html>
```